Business card

We need a business card design for our company based in Auckland , New Zealand called 'Harrow Lane Design Ltd'. We provide architectural services. We would like to see designs that use the max. three colours (such as white, black, grey) The final design should communicate financial safety and growth."
Also I will provide our company logo. I would like to the logo to be embeded onto our business card.

Target Market(s)

new residential house, alteration & addition & light commericila design & drafting service

Industry/Entity Type

Architecture

Contact Information for Business Card

Company name: harrow lane design Ltd.
Name: Mark Delford
Job title: architectural designer & Design Lead
email address: mark@harrowlane.co.nz
mobile number: 02 5163 2290
web site: www.harrowlane.co.nz

Requirements
Must have
• My project must have..
• - embeded logo (attached company logo)
• I don't have a bigger version for our company logo, but I have one old one, so you can remove the word from it)
• - insert the attached small BKTW logo & LBP logo
• - creative, simple and clear business card.
• - Max. three colours
Nice to have
• - Here are the samples I would like to share with you: http://www.plimvora.com/blog/minimalistic-business-card-designs/
• I would like to have my business card like one of the creation.
Should not have
• TBA

```html
<!DOCTYPE html>
<html lang="en">
<head>
<meta charset="utf-8">
<title>Harrow Lane Design Ltd — Business Card</title>
<link rel="stylesheet" href="https://fonts.googleapis.com/css2?family=Roboto+Condensed:wght@300;400&display=swap">
<style>
  :root {
    --stage: #2b2b2d;
    --card-black: #0b0b0b;
    --card-white: #f4f4f4;
    --ink-light: #e9e9e9;
    --ink-dark: #111111;
  }
  * { margin: 0; padding: 0; box-sizing: border-box; }
  html, body {
    width: 1200px;
    height: 950px;
    overflow: hidden;
    background: var(--stage);
  }
  .canvas {
    width: 1200px;
    height: 950px;
    display: flex;
    flex-direction: column;
    align-items: center;
    justify-content: center;
    gap: 50px;
  }
  .card {
    width: 700px;
    height: 400px;
    border-radius: 4px;
    position: relative;
    overflow: hidden;
    box-shadow: 0 10px 30px rgba(0,0,0,0.45);
  }

  /* Back side */
  .card--back {
    background: linear-gradient(135deg, #ffffff 0%, var(--card-white) 55%, #d9d9d9 100%);
    display: flex;
    align-items: center;
    justify-content: center;
  }
  .brand-mark {
    display: flex;
    align-items: center;
    gap: 20px;
    color: var(--ink-dark);
    font-family: "Roboto Condensed", sans-serif;
    font-weight: 300;
    font-size: 40px;
    letter-spacing: 1px;
  }
  .brand-mark__dot {
    width: 24px;
    height: 24px;
    border-radius: 50%;
    background: var(--ink-dark);
  }

  /* Front side */
  .card--front {
    background: linear-gradient(160deg, #1c1c1c 0%, var(--card-black) 40%, #000 100%);
    color: var(--ink-light);
    font-family: "Roboto Condensed", sans-serif;
    font-weight: 300;
  }
  .cert-badge {
    position: absolute;
    left: 40px;
    top: 36px;
    width: 92px;
    height: 92px;
  }
  .association-name {
    position: absolute;
    left: 44px;
    bottom: 56px;
    font-weight: 400;
    font-size: 34px;
    letter-spacing: 1px;
  }
  .contact {
    position: absolute;
    left: 330px;
    top: 92px;
  }
  .contact__name {
    font-size: 30px;
    letter-spacing: 0.5px;
    line-height: 1.15;
  }
  .contact__title {
    font-size: 26px;
    line-height: 1.2;
    margin-bottom: 22px;
  }
  .contact__company {
    font-size: 21px;
    margin-bottom: 8px;
  }
  .contact__list {
    list-style: none;
    font-size: 21px;
    line-height: 1.45;
  }
  .contact__item {
    display: flex;
    align-items: center;
    gap: 10px;
  }
  .contact__icon {
    width: 16px;
    height: 16px;
    flex: none;
  }
</style>
</head>
<body>
<main class="canvas">

  <section class="card card--back" aria-label="Business card back">
    <div class="brand-mark">
      <span class="brand-mark__dot"></span>
      <span class="brand-mark__name">Harrow Lane Design Ltd</span>
    </div>
  </section>

  <section class="card card--front" aria-label="Business card front">
    <svg class="cert-badge" viewBox="0 0 92 92" role="img" aria-label="Practitioner certification badge">
      <circle cx="46" cy="46" r="45" fill="#ffffff"/>
    </svg>

    <div class="association-name">BKTW</div>

    <div class="contact">
      <p class="contact__name">MARK DELFORD</p>
      <p class="contact__title">architectural designer &amp;<br>Design Lead</p>
      <p class="contact__company">harrow lane design Ltd.</p>
      <ul class="contact__list">
        <li class="contact__item">
          <svg class="contact__icon" viewBox="0 0 16 16" aria-hidden="true">
            <rect x="3.5" y="1" width="9" height="14" rx="1.5" fill="none" stroke="#e9e9e9" stroke-width="1.4"/>
            <line x1="6.5" y1="12.5" x2="9.5" y2="12.5" stroke="#e9e9e9" stroke-width="1.2"/>
          </svg>
          <span>02 5163 2290</span>
        </li>
        <li class="contact__item">
          <svg class="contact__icon" viewBox="0 0 16 16" aria-hidden="true">
            <rect x="1" y="3" width="14" height="10" fill="#e9e9e9"/>
            <polyline points="1,3 8,9 15,3" fill="none" stroke="#0b0b0b" stroke-width="1.3"/>
          </svg>
          <span>mark@harrowlane.co.nz</span>
        </li>
        <li class="contact__item">
          <svg class="contact__icon" viewBox="0 0 16 16" aria-hidden="true">
            <circle cx="8" cy="8" r="7.5" fill="#e9e9e9"/>
            <circle cx="8" cy="8" r="3" fill="#0b0b0b"/>
          </svg>
          <span>www.harrowlane.co.nz</span>
        </li>
      </ul>
    </div>
  </section>

</main>
</body>
</html>
```